Fresh and unique Mortgage Broking business needs website design.

We need a professional yet fresh, bright and colourful website for my Mortgage broking business.
We specialise in the Non conforming/sub prime market with clients who have been rejected by other banks or have trouble getting finance through a traditional lender.
We are called Lark Lending and we aim to provide Hope to our clients when they have thought there was no hope.
I would like it to be on a Wordpress platform as I plan to do a lot of postings, both written and video and I need it to be easy to use.
I would also like it to be able to have a clear and simple enquiry box on the first page to capture contact details and notify me via email.

I have already had the logo designed in both green and black and a white version.
I have also had a a header made up using the white logo with leaves background that could possibly be used as the website header which I have used as my facebook header.

https://www.pagebook-example.com/MarcusDellowLark/

I tried playing around with a sitebuild website builder which kind of got some of the brightness and colours I was after but it had a lot to go.

http://larklending.sitebuildexample.com/

Industry/Entity Type

Finance

Number of Pages Required

4 page

Colors
0292cd
00a990
fbed22
ffc214
f78f20
ec1f27

Requirements
Nice to have
• I'm not sure what the difference between uncoded and coded website is so I'm not sure what I need?

```html
<!DOCTYPE html>
<html lang="en">
<head>
<meta charset="utf-8">
<title>Lark Lending</title>
<link rel="stylesheet" href="https://fonts.googleapis.com/css2?family=Roboto+Slab:wght@300;400&family=Roboto:wght@400;500&family=Montserrat:wght@400;500&display=swap">
<style>
:root{
  --blue:#0292cd;
  --teal:#00a990;
  --yellow:#fbed22;
  --amber:#ffc214;
  --orange:#f78f20;
  --red:#ec1f27;
  --ink:#3a3a3a;
  --muted:#666;
  --line:#e3e3e3;
  --paper:#f5f6f8;
  --footer:#f3f4f6;
  --bar:#4b4b4b;
  --green:#1f7a3a;
}
*{box-sizing:border-box;margin:0;padding:0}
html,body{width:1200px;height:2571px;overflow:hidden}
body{position:relative;background:#fff;font-family:"Roboto Slab",Georgia,serif;color:var(--ink)}
h1,h2,h3,h4{font-weight:400}
.abs{position:absolute}

/* hero */
.hero{left:0;top:0;width:1200px;height:651px;
  background:radial-gradient(circle at 78% 18%,#e8561a 0,#b8321a 18%,transparent 40%),
             radial-gradient(circle at 30% 60%,#9aa03a 0,#6a6a2a 30%,transparent 60%),
             linear-gradient(120deg,#c05a1c 0%,#8a6a2a 35%,#6b3a18 60%,#2a120c 100%)}
.hero-brand{left:64px;top:380px;color:#fff;font-family:"Roboto Slab",serif;font-weight:300;font-size:96px;letter-spacing:6px;line-height:1}

/* nav */
.nav{left:0;top:651px;width:1200px;height:74px;background:linear-gradient(#ffd21f,#ffb514);display:flex;align-items:center;padding-left:86px}
.nav-item{height:74px;display:flex;align-items:center;justify-content:center;color:#fff;font-family:Montserrat,Arial,sans-serif;font-size:14px;font-weight:500;border-right:1px solid rgba(255,255,255,.35);white-space:nowrap}
.nav-item:last-child{border-right:none}
.search{left:867px;top:672px;width:233px;height:37px;background:#fff;border-radius:3px;font-family:Roboto,Arial,sans-serif;font-size:14px;color:#888;padding:10px 16px}
.search svg{position:absolute;right:14px;top:12px}

/* sections */
.section-title{width:1200px;left:0;text-align:center;font-size:30px;font-weight:400;color:#333}
.section-lead{width:640px;left:280px;text-align:center;font-size:13px;line-height:24px;color:#666;font-weight:300}
.services{left:0;top:725px;width:1200px;height:538px;background:var(--paper)}

.card{top:876px;width:242px;height:336px;background:#fff;border:1px solid var(--line);border-bottom:4px solid var(--c);text-align:center;box-shadow:0 1px 3px rgba(0,0,0,.06)}
.card-icon{margin:18px auto 0;width:112px;height:112px;border-radius:50%;background:var(--c);border:4px solid #fff;box-shadow:0 0 0 2px var(--c);display:flex;align-items:center;justify-content:center}
.card-title{margin-top:18px;font-size:17px;line-height:22px;color:var(--c);white-space:nowrap}
.card-text{margin:12px auto 0;width:226px;font-family:Roboto,Arial,sans-serif;font-size:12.5px;line-height:24px;color:#555;white-space:nowrap}
.btn{display:inline-block;border:1px solid var(--c);color:var(--c);font-size:14px;line-height:16px;padding:10px 0;margin-top:8px;width:108px;text-align:center}

.welcome{left:0;top:1263px;width:1200px;height:388px;background:linear-gradient(90deg,#eaeaea,#f2f2f2 55%,#f5f5f5)}
.welcome-photo{left:686px;top:1263px;width:514px;height:388px;background:linear-gradient(180deg,#f4f4f4,#e9e9e9 60%,#dedede)}
.welcome-title{left:86px;top:1296px;font-size:30px;color:#333}
.welcome-text{left:86px;width:450px;font-size:13px;line-height:24px;color:#555;font-weight:300}
.btn-amber{left:86px;top:1586px;width:128px;height:42px;border:1px solid var(--amber);color:var(--amber);font-size:14px;text-align:center;line-height:40px}

.news-img{top:1810px;width:326px;height:206px}
.news-title{top:2040px;font-size:15px;color:#333;width:326px}
.news-meta{top:2078px;width:326px;height:36px;border-top:1px solid var(--line);border-bottom:1px solid var(--line);display:flex;justify-content:space-between;align-items:center;padding:0 4px;font-family:Roboto,Arial,sans-serif;font-size:10px;color:#777}
.news-text{top:2128px;width:326px;font-family:Roboto,Arial,sans-serif;font-size:12.5px;line-height:26px;color:#555}

/* footer */
.footer{left:0;top:2241px;width:1200px;height:262px;background:var(--footer)}
.foot-brand{left:86px;top:2340px;font-family:"Roboto Slab",serif;font-size:44px;color:var(--green);font-weight:400}
.foot-h{top:2280px;font-family:Roboto,Arial,sans-serif;font-size:15px;font-weight:500;color:#444;letter-spacing:.5px}
.contact-row{left:403px;font-family:Roboto,Arial,sans-serif;font-size:12px;color:#666;display:flex;gap:12px;align-items:flex-start;width:230px;line-height:17px}
.news-note{left:648px;top:2320px;width:220px;font-size:12px;line-height:20px;color:#666}
.email-box{left:648px;top:2378px;width:213px;height:34px;border:1px solid #ccc;background:#fff;font-family:Roboto,Arial,sans-serif;font-size:12px;color:#555;padding:9px 14px}
.subscribe{left:648px;top:2420px;width:82px;height:28px;background:var(--red);color:#fff;font-family:Roboto,Arial,sans-serif;font-size:10px;text-align:center;line-height:28px}
.follow-text{left:907px;top:2322px;width:200px;font-family:Roboto,Arial,sans-serif;font-size:11px;line-height:19px;color:#777}
.social{left:905px;top:2402px;display:flex;gap:9px}
.social span{width:34px;height:34px;border-radius:50%;border:1.5px solid #aaa}
.bottom-bar{left:0;top:2503px;width:1200px;height:68px;background:var(--bar);color:#fff;text-align:center;font-family:Roboto,Arial,sans-serif;font-size:13px;line-height:68px}
</style>
</head>
<body>

<header>
  <div class="abs hero" role="img" aria-label="Close-up of autumn maple leaves in red and orange against a soft blurred background"></div>
  <div class="abs hero-brand">Lark Lending</div>

  <nav class="abs nav">
    <span class="nav-item" style="width:128px">HOME</span>
    <span class="nav-item" style="width:132px">ABOUT</span>
    <span class="nav-item" style="width:151px">SERVICES</span>
    <span class="nav-item" style="width:219px">PROPERTY ADVICE</span>
    <span class="nav-item" style="width:146px">CONTACT</span>
  </nav>
  <div class="abs search">Search
    <svg width="12" height="12" viewBox="0 0 12 12"><circle cx="5" cy="5" r="3.6" fill="none" stroke="#666" stroke-width="1.5"/><line x1="7.7" y1="7.7" x2="11" y2="11" stroke="#666" stroke-width="1.5"/></svg>
  </div>
</header>

<main>
  <section class="abs services"></section>
  <h2 class="abs section-title" style="top:756px">Our Services</h2>
  <p class="abs section-lead" style="top:804px">I would highly recommend Marcus from Lark Lending! Excellent customer service and was always our questions. He has made the purchase of our dream home a reality.</p>

  <article class="abs card" style="left:86px;--c:var(--blue)">
    <div class="card-icon">
      <svg width="56" height="56" viewBox="0 0 56 56" fill="none" stroke="#fff" stroke-width="3"><path d="M10 26 L28 10 L46 26"/><path d="M16 22 V44 H40 V22"/><text x="28" y="39" fill="#fff" stroke="none" font-size="18" text-anchor="middle" font-family="Arial">$</text></svg>
    </div>
    <h3 class="card-title">Residential loans</h3>
    <p class="card-text">I would highly recommend Marcus<br>from Lark Lending! Excellent custo<br>mer service and was always</p>
    <span class="btn">Read More</span>
  </article>

  <article class="abs card" style="left:348px;--c:var(--teal)">
    <div class="card-icon">
      <svg width="56" height="56" viewBox="0 0 56 56" fill="none" stroke="#fff" stroke-width="3"><path d="M22 8 H34 L30 16 H26 Z"/><path d="M26 16 C12 24 12 48 28 48 C44 48 44 24 30 16"/><text x="28" y="42" fill="#fff" stroke="none" font-size="18" text-anchor="middle" font-family="Arial">$</text></svg>
    </div>
    <h3 class="card-title">Investment loans</h3>
    <p class="card-text">I would highly recommend Marcus<br>from Lark Lending! Excellent custo<br>mer service and was always</p>
    <span class="btn">Read More</span>
  </article>

  <article class="abs card" style="left:610px;--c:var(--amber)">
    <div class="card-icon">
      <svg width="56" height="56" viewBox="0 0 56 56" fill="none" stroke="#fff" stroke-width="3"><rect x="14" y="14" width="28" height="18" rx="2"/><path d="M8 38 H48"/><path d="M14 38 V48 M42 38 V48"/></svg>
    </div>
    <h3 class="card-title">Self employed loans</h3>
    <p class="card-text">I would highly recommend Marcus<br>from Lark Lending! Excellent custo<br>mer service and was always</p>
    <span class="btn">Read More</span>
  </article>

  <article class="abs card" style="left:872px;--c:var(--red)">
    <div class="card-icon">
      <svg width="56" height="56" viewBox="0 0 56 56"><path d="M14 8 H36 L44 16 V48 H14 Z" fill="#fff"/><path d="M22 26 L29 20 L36 26 V32 H22 Z" fill="var(--red)"/><rect x="20" y="37" width="18" height="2.5" fill="var(--red)"/><rect x="20" y="42" width="18" height="2.5" fill="var(--red)"/></svg>
    </div>
    <h3 class="card-title">Non confirming loans</h3>
    <p class="card-text">I would highly recommend Marcus<br>from Lark Lending! Excellent custo<br>mer service and was always</p>
    <span class="btn">Read More</span>
  </article>

  <section class="abs welcome"></section>
  <div class="abs welcome-photo" role="img" aria-label="Woman seen from behind working at a white desk in a bright minimal office"></div>
  <h2 class="abs welcome-title">Welcome to Lark Lending</h2>
  <p class="abs welcome-text" style="top:1356px">I would highly recommend Marcus from Lark Lending! Excellent customer service and was always our questions. He has made the purchase of our dream home a reality. sed ut perspiciatis unde omnis iste natus error sit ue ipsa quae ab illo inventore veritatis et quasi architecto</p>
  <p class="abs welcome-text" style="top:1476px">Beatae vitae dicta sunt explicabo. Nemo enim ipsam voluptatem quia vol uptas sit aspernatur aut odit aut fugit, sed quia consequuntur magni dolor eos qui ratione voluptatem sequi nesciunt.</p>
  <span class="abs btn-amber">Read More</span>

  <h2 class="abs section-title" style="top:1680px">Latest News</h2>
  <p class="abs section-lead" style="top:1733px;width:720px;left:240px">I would highly recommend Marcus from Lark Lending! Excellent customer service and was always our questions. He has made the purchase of our dream home a reality.</p>

  <div class="abs news-img" style="left:86px;background:linear-gradient(180deg,#5a9ee0,#bcd9f2 45%,#e9c9a8 80%,#f2e3d2)" role="img" aria-label="Hands holding a small house on a patch of grass under a blue sky"></div>
  <div class="abs news-img" style="left:437px;background:linear-gradient(135deg,#3a2618,#8a5a30 40%,#d9a060 60%,#5a4030)" role="img" aria-label="Laptop on a desk with a hand writing in warm evening light"></div>
  <div class="abs news-img" style="left:789px;background:linear-gradient(160deg,#5a5050,#b8b0a8 45%,#e6e2dc 75%,#c8c0b6)" role="img" aria-label="Office desk with boxes and papers in a bright workspace"></div>

  <h3 class="abs news-title" style="left:86px">How Much Deposit Do I Need</h3>
  <h3 class="abs news-title" style="left:437px">How Much Deposit Do I Need</h3>
  <h3 class="abs news-title" style="left:789px">How Much Deposit Do I Need</h3>

  <div class="abs news-meta" style="left:86px"><span>◷ 27 MARCH 2016</span><span>▭ 120</span><span>♡ LIKE</span><span>↗ SHARE</span></div>
  <div class="abs news-meta" style="left:437px"><span>◷ 27 MARCH 2016</span><span>▭ 120</span><span>♡ LIKE</span><span>↗ SHARE</span></div>
  <div class="abs news-meta" style="left:789px"><span>◷ 27 MARCH 2016</span><span>▭ 120</span><span>♡ LIKE</span><span>↗ SHARE</span></div>

  <p class="abs news-text" style="left:86px">Sed ut perspiciatis unde omnis iste natus error sit volupta tem accusantium doloremque laudantium, totam rem arch itecto beatae vitae dicta sunt explicabo.</p>
  <p class="abs news-text" style="left:437px">Sed ut perspiciatis unde omnis iste natus error sit volupta tem accusantium doloremque laudantium, totam rem arch itecto beatae vitae dicta sunt explicabo.</p>
  <p class="abs news-text" style="left:789px">Sed ut perspiciatis unde omnis iste natus error sit volupta tem accusantium doloremque laudantium, totam rem arch itecto beatae vitae dicta sunt explicabo.</p>
</main>

<footer>
  <div class="abs footer"></div>
  <div class="abs foot-brand">Lark Lending</div>

  <h4 class="abs foot-h" style="left:403px">CONTACT US</h4>
  <div class="abs contact-row" style="top:2328px">
    <svg width="13" height="13" viewBox="0 0 13 13"><path d="M3 1 L5 4 L4 5 C5 7 6 8 8 9 L9 8 L12 10 L11 12 C6 12 1 7 1 2 Z" fill="#777"/></svg><span>Phone - 0400 512 374</span></div>
  <div class="abs contact-row" style="top:2357px">
    <svg width="13" height="13" viewBox="0 0 13 13"><rect x="1" y="4" width="11" height="6" fill="#777"/><rect x="3" y="1" width="7" height="3" fill="#777"/><rect x="3" y="9" width="7" height="3" fill="#999"/></svg><span>Fax - (03) 9012 6638</span></div>
  <div class="abs contact-row" style="top:2386px">
    <svg width="13" height="13" viewBox="0 0 13 13"><rect x="1" y="3" width="11" height="8" fill="#777"/><path d="M1 3 L6.5 8 L12 3" fill="none" stroke="#fff" stroke-width="1"/></svg><span style="text-decoration:underline">Email-info@larklending.example</span></div>
  <div class="abs contact-row" style="top:2414px">
    <svg width="13" height="13" viewBox="0 0 13 13"><path d="M6.5 12 C3 8 2 6 2 4.5 A4.5 4.5 0 0 1 11 4.5 C11 6 10 8 6.5 12 Z" fill="#777"/><circle cx="6.5" cy="4.5" r="1.6" fill="#fff"/></svg><span>Meridian | 45 Sample Lane | Springfi eld, CA 90210</span></div>

  <h4 class="abs foot-h" style="left:648px">NEWSLETTER</h4>
  <p class="abs news-note">Register Your email address to get information ablout us</p>
  <div class="abs email-box">Email Address</div>
  <div class="abs subscribe">SUBSCRIBE</div>

  <h4 class="abs foot-h" style="left:907px">FOLLOW US</h4>
  <p class="abs follow-text">Lorem ipsum dolor sit amet, conse ctetur adipiscing elit. Nulla in purus nibh. Donec ornare</p>
  <div class="abs social"><span></span><span></span><span></span><span></span><span></span></div>

  <div class="abs bottom-bar">© Copyright 2016 Lark Lending.All Rights Reserved</div>
</footer>

</body>
</html>
```